High Tech Real Estate Startup needs a business card

We are developing an innovative real estate marketing product based around advanced search and virtual reality.

We talk to people, we need business cards.

Target Market(s)

The target market is technology professionals and realtors.

Contact Information for Business Card

The information to be included will include

Name
Title
Phone Number
E-mail Address
www.zelquin.com

It should use simple iconography for each one of those fields.

Font styles to use
Other font styles liked:
• Co, Jubilat, Avenir

Colors

Designer to choose colors to be used in the design.

Requirements
Must have
• Clean aesthetic,
• Good use of negative space.
• It should use our company logo, shown in the attached file. It is able to use the negative of that logo (coloured font and white background) and I have attached other acceptable accent colours in a swatch file.
Should not have
• Should not be too busy
• No extraneous text (slogans, tag lines etc)

```html
<!DOCTYPE html>
<html lang="en">
<head>
<meta charset="utf-8">
<title>Zelquin Business Card</title>
<link rel="stylesheet" href="https://fonts.googleapis.com/css2?family=Open+Sans:wght@400;600&display=swap">
<style>
  :root {
    --backdrop: #2b2b2d;
    --card-teal: #3ba7a9;
    --logo-teal: #2b8587;
    --ink-white: #ffffff;
    --icon-fill: #ffffff;
  }
  * { margin: 0; padding: 0; box-sizing: border-box; }
  html, body {
    width: 799px;
    height: 1200px;
    overflow: hidden;
    background: var(--backdrop);
    font-family: "Open Sans", Arial, sans-serif;
  }
  .sheet {
    position: relative;
    width: 799px;
    height: 1200px;
  }
  .card {
    position: absolute;
    left: 90px;
    width: 620px;
    height: 354px;
    background: var(--card-teal);
    border-radius: 26px;
  }
  .card--front { top: 110px; }
  .card--back { top: 720px; }

  .brand-name {
    position: absolute;
    left: 0;
    right: 0;
    top: 138px;
    text-align: center;
    font-size: 66px;
    font-weight: 600;
    letter-spacing: 4px;
    color: var(--logo-teal);
    line-height: 1;
  }

  .identity {
    position: absolute;
    left: 120px;
    top: 140px;
    color: var(--ink-white);
    text-align: right;
    width: 180px;
  }
  .identity__name {
    font-size: 22px;
    font-weight: 600;
    line-height: 1.2;
    white-space: nowrap;
  }
  .identity__title {
    font-size: 14px;
    font-weight: 400;
    margin-top: 4px;
    white-space: nowrap;
  }

  .divider {
    position: absolute;
    left: 322px;
    top: 118px;
    width: 1.5px;
    height: 118px;
    background: var(--ink-white);
  }

  .contacts {
    position: absolute;
    left: 344px;
    top: 140px;
    list-style: none;
    color: var(--ink-white);
  }
  .contacts__item {
    display: flex;
    align-items: center;
    gap: 10px;
    height: 24px;
    font-size: 15px;
    font-weight: 400;
  }
  .contacts__icon {
    width: 18px;
    height: 18px;
    flex: none;
  }
</style>
</head>
<body>
<main class="sheet">
  <section class="card card--front" aria-label="Card front">
    <div class="brand-name">ZELQUIN</div>
  </section>

  <section class="card card--back" aria-label="Card back">
    <div class="identity">
      <p class="identity__name">John Doe Smith</p>
      <p class="identity__title">Managing Director</p>
    </div>

    <div class="divider"></div>

    <ul class="contacts">
      <li class="contacts__item">
        <svg class="contacts__icon" viewBox="0 0 18 18" aria-hidden="true">
          <circle cx="9" cy="9" r="9" fill="var(--icon-fill)"/>
          <path d="M5.5 5.2c.4-.4 1-.4 1.3 0l1 1.2c.3.4.2.8-.1 1.1l-.5.5c.5 1 1.2 1.7 2.2 2.2l.5-.5c.3-.3.8-.4 1.1-.1l1.2 1c.4.3.4.9 0 1.3l-.6.6c-.6.6-3 .1-4.6-1.5S4.3 6.4 4.9 5.8z" fill="var(--card-teal)"/>
        </svg>
        <span>555.555.5555</span>
      </li>
      <li class="contacts__item">
        <svg class="contacts__icon" viewBox="0 0 18 18" aria-hidden="true">
          <circle cx="9" cy="9" r="9" fill="var(--icon-fill)"/>
          <rect x="4.5" y="5.8" width="9" height="6.4" rx="0.8" fill="none" stroke="var(--card-teal)" stroke-width="1.2"/>
          <path d="M4.8 6.3 9 9.4l4.2-3.1" fill="none" stroke="var(--card-teal)" stroke-width="1.2"/>
        </svg>
        <span>johndoe@zelquin.com</span>
      </li>
      <li class="contacts__item">
        <svg class="contacts__icon" viewBox="0 0 18 18" aria-hidden="true">
          <circle cx="9" cy="9" r="9" fill="var(--icon-fill)"/>
          <circle cx="9" cy="9" r="4.6" fill="none" stroke="var(--card-teal)" stroke-width="1.1"/>
          <ellipse cx="9" cy="9" rx="2" ry="4.6" fill="none" stroke="var(--card-teal)" stroke-width="1.1"/>
          <path d="M4.4 9h9.2" stroke="var(--card-teal)" stroke-width="1.1"/>
        </svg>
        <span>www.zelquin.com</span>
      </li>
    </ul>
  </section>
</main>
</body>
</html>
```